creation of a business card design for a company specializing in the creation...

I would like to create a design for a professional business card on a black background and with the company's colors (I am attaching some files: including the logo in horizontal and centered format, I am also attaching a recent project design a T-shirt, this is the one I chose to give you an idea of my preferences.

we are in the process of developing a new website design, it is still in the development phase but it can be viewed at the following address: www.vantrelmo.be to give you other ideas about the company
you will see for yourself the subject of my main activity: company specializing in the construction of stairs

I would like a business card that stands out from the rest with a unique design

here is the informations
Name: Lucien Barthel
Function: Manager
Address: Rue Moulinet du Parc 42
7180 La Louvière
telephone: +32 468 219 804
email: info@rx7p.be
website: rx7p. be
social networks: Facebook, YouTube, TikTok, Instagram

Target Market(s)

customer who wants to have a beautiful staircase built

Industry/Entity Type

contruction d'escalier

Contact Information for Business Card

Adresse. Numero de telephone, site web, le texte : "Createur d'escalier", logo recto-verso, icone des reseaux sociaux

Requirements
Must have
• the mention: Stair creator
Nice to have
• an illustration of a designer staircase
Should not have
• do not distort the logo

```html
<!DOCTYPE html>
<html lang="fr">
<head>
<meta charset="utf-8">
<title>RX7P – Cartes de visite</title>
<link rel="stylesheet" href="https://fonts.googleapis.com/css2?family=Open+Sans:wght@400;600;700&display=swap">
<style>
  :root {
    --stage: #2a2e33;
    --card-black: #0d0d0e;
    --card-edge: #1b1c1e;
    --steel-blue: #4a7488;
    --steel-blue-dark: #2f5264;
    --steel-blue-light: #8fb4c6;
    --text-white: #f4f6f7;
    --text-soft: #c9d2d7;
    --dot: #e6ebee;
  }
  * { margin: 0; padding: 0; box-sizing: border-box; }
  html, body { width: 1200px; height: 780px; overflow: hidden; }
  body {
    background: var(--stage);
    font-family: "Open Sans", Arial, sans-serif;
    position: relative;
  }
  .card {
    position: absolute;
    top: 230px;
    width: 560px;
    height: 320px;
    background: linear-gradient(160deg, var(--card-edge) 0%, var(--card-black) 60%);
    overflow: hidden;
  }
  .card--front { left: 20px; }
  .card--back { left: 620px; }

  /* Front */
  .social-band {
    position: absolute; left: 0; top: 0; bottom: 0; width: 62px;
    background: linear-gradient(180deg, var(--steel-blue) 0%, var(--steel-blue-dark) 100%);
  }
  .social-band__inner {
    position: absolute; left: 50%; bottom: 40px;
    transform-origin: left center;
    transform: translateX(10px) rotate(-90deg);
    display: flex; align-items: center; gap: 10px;
    white-space: nowrap;
  }
  .social-band__label { color: var(--text-white); font-size: 17px; font-weight: 400; letter-spacing: 0.5px; }
  .social-band__dot { width: 15px; height: 15px; border-radius: 50%; background: var(--dot); }

  .brand {
    position: absolute; right: 40px; top: 34px;
    display: flex; align-items: center; gap: 12px;
  }
  .brand__square { width: 34px; height: 34px; background: var(--steel-blue-light); }
  .brand__name { color: var(--text-white); font-size: 40px; font-weight: 400; letter-spacing: 4px; line-height: 1; }

  .person {
    position: absolute; right: 40px; top: 112px; text-align: right;
  }
  .person__name { color: var(--text-white); font-size: 27px; font-weight: 700; line-height: 1.1; }
  .person__role { color: var(--text-white); font-size: 16px; font-weight: 400; margin-top: 2px; }

  .accent-steps { position: absolute; right: 0; top: 118px; }

  .contact {
    position: absolute; right: 40px; top: 186px; text-align: right;
    color: var(--text-white); font-size: 15px; line-height: 22px;
  }
  .contact__address { margin-bottom: 6px; }
  .contact__row { display: flex; justify-content: flex-end; align-items: center; gap: 8px; }
  .contact__icon { width: 15px; height: 15px; flex: none; }

  /* Back */
  .badge {
    position: absolute; left: 50%; top: 38px; transform: translateX(-50%);
    width: 190px; height: 190px; border-radius: 50%;
    background: radial-gradient(circle at 50% 45%, #6f8b99 0%, var(--steel-blue) 45%, var(--steel-blue-dark) 80%, #1d2d36 100%);
  }
  .badge-caption {
    position: absolute; left: 0; right: 0; text-align: center;
  }
  .badge-caption--tagline { top: 16px; color: var(--text-white); font-size: 13px; font-weight: 700; letter-spacing: 1px; text-transform: uppercase; }
  .badge-caption--brand { top: 236px; color: var(--text-white); font-size: 30px; font-weight: 400; letter-spacing: 4px; }
  .badge-caption--contact { top: 278px; color: var(--text-soft); font-size: 11px; font-weight: 600; letter-spacing: 0.5px; }
</style>
</head>
<body>

  <section class="card card--front" aria-label="Recto de la carte">
    <div class="social-band">
      <div class="social-band__inner">
        <span class="social-band__label">Follow us:</span>
        <span class="social-band__dot" aria-hidden="true"></span>
        <span class="social-band__dot" aria-hidden="true"></span>
        <span class="social-band__dot" aria-hidden="true"></span>
        <span class="social-band__dot" aria-hidden="true"></span>
      </div>
    </div>

    <div class="brand">
      <span class="brand__square"></span>
      <span class="brand__name">RX7P</span>
    </div>

    <div class="person">
      <p class="person__name">Lucien Barthel</p>
      <p class="person__role">Manager</p>
    </div>

    <svg class="accent-steps" width="22" height="54" viewBox="0 0 22 54" aria-hidden="true">
      <rect x="0" y="0" width="22" height="14" fill="var(--steel-blue)"/>
      <rect x="4" y="18" width="18" height="14" fill="var(--steel-blue)" opacity="0.85"/>
      <rect x="8" y="36" width="14" height="14" fill="var(--steel-blue-dark)"/>
    </svg>

    <div class="contact">
      <div class="contact__address">
        <p>Rue Moulinet du Parc 42</p>
        <p>7180 La Louvière</p>
      </div>
      <p class="contact__row">+32 468 219 804
        <svg class="contact__icon" viewBox="0 0 16 16" aria-hidden="true"><path d="M4 1.5 6.2 4 5 5.6c.8 1.9 2.4 3.5 4.4 4.4L11 8.8l2.5 2.2-1.3 2.5C7 13.3 2.7 9 2.5 3.8z" fill="var(--steel-blue-light)"/></svg>
      </p>
      <p class="contact__row">info@rx7p.be
        <svg class="contact__icon" viewBox="0 0 16 16" aria-hidden="true"><rect x="1.5" y="3.5" width="13" height="9" rx="1" fill="none" stroke="var(--steel-blue-light)" stroke-width="1.5"/><path d="M2 4l6 5 6-5" fill="none" stroke="var(--steel-blue-light)" stroke-width="1.5"/></svg>
      </p>
      <p class="contact__row">www.rx7p.be
        <svg class="contact__icon" viewBox="0 0 16 16" aria-hidden="true"><circle cx="8" cy="8" r="6.3" fill="none" stroke="var(--steel-blue-light)" stroke-width="1.4"/><ellipse cx="8" cy="8" rx="2.6" ry="6.3" fill="none" stroke="var(--steel-blue-light)" stroke-width="1.2"/><path d="M1.8 8h12.4" stroke="var(--steel-blue-light)" stroke-width="1.2"/></svg>
      </p>
    </div>
  </section>

  <section class="card card--back" aria-label="Verso de la carte">
    <p class="badge-caption badge-caption--tagline">Créateur d'escalier</p>
    <div class="badge" role="img" aria-label="Emblème circulaire avec l'illustration d'un escalier design en perspective"></div>
    <p class="badge-caption badge-caption--brand">RX7P</p>
    <p class="badge-caption badge-caption--contact">0468 219 804 &nbsp;·&nbsp; RX7P.BE</p>
  </section>

</body>
</html>
```